Harborview Optical -Window Poster (Optometrist)

We are an optometry practice and we need a poster for a new store promotion for our window highlighting we now also sell 2 pairs of glasses as a package deal. The size will be 1300mm width x 1900mm height

The artwork will be displayed as a fabric banner in our shop window. We have 7 other banners with different services our business provides. The words needs to standout for passers by and the cars stopped at the traffic lights out front of our business. We already have signs with our logos phone number etc. so we won't need them included in the poster.

It would need to include the following information.

Two pair packages now available*

*Conditions apply

The artwork will be displayed as a fabric banner in our shop window. We have 7 other banners with different services our business provides. The words needs to standout for passers by and the cars stopped at the traffic lights out front of our business. We already have signs with our logos phone number etc. so we won't need them included in the poster. Thank you for your work it's amazing Added Saturday, February 18, 2017

The artwork will be displayed as a fabric banner in our shop window. We have 7 other banners with different services our business provides. The words needs to standout for passers by and the cars stopped at the traffic lights out front of our business. We already have signs with our logos phone number etc. so we won't need them included in the poster. Added Saturday, February 18, 2017

Target Market(s)

Cars driving past and stopped at traffic lights outside our store.

Industry/Entity Type

Optician

Requirements
Must have
• Poster must say:
• Two pair packages now available*
• *Conditions apply

```html
<!DOCTYPE html>
<html lang="en">
<head>
<meta charset="utf-8">
<title>Harborview Optical – Two Pair Packages Window Poster</title>
<link rel="stylesheet" href="https://fonts.googleapis.com/css2?family=Anton&family=Bebas+Neue&family=Montserrat:wght@600&display=swap">
<style>
  :root {
    --poster-black: #050505;
    --alert-red: #ee1c25;
    --signal-yellow: #fff200;
    --band-grey: rgba(214, 211, 214, 0.86);
    --label-navy: #0b1130;
    --iris-light: #5cc8f2;
    --iris-mid: #12a8e6;
    --iris-deep: #1f67c4;
    --white: #ffffff;
    --streak: rgba(120, 140, 170, 0.35);
  }
  * { margin: 0; padding: 0; box-sizing: border-box; }
  html, body { width: 962px; height: 1200px; overflow: hidden; background: var(--poster-black); }

  .poster {
    position: relative;
    width: 962px;
    height: 1200px;
    background: var(--poster-black);
    overflow: hidden;
  }

  .streak {
    position: absolute;
    height: 3px;
    border-radius: 2px;
    background: linear-gradient(90deg, transparent, var(--streak), transparent);
  }
  .streak--top { left: 0; top: 52px; width: 360px; }
  .streak--upper { left: 480px; top: 173px; width: 482px; }
  .streak--lower { left: 0; top: 1003px; width: 500px; }

  .headline-tag {
    position: absolute;
    right: 30px;
    top: 80px;
    font-family: "Bebas Neue", sans-serif;
    font-size: 77px;
    line-height: 1;
    letter-spacing: 3px;
    color: var(--alert-red);
  }

  .iris-art {
    position: absolute;
    left: 0;
    top: 0;
  }

  .offer-band {
    position: absolute;
    left: 37px;
    top: 391px;
    width: 902px;
    height: 188px;
    background: var(--band-grey);
    display: flex;
    align-items: center;
    justify-content: center;
  }
  .offer-band__title {
    font-family: "Anton", sans-serif;
    font-size: 166px;
    line-height: 1;
    letter-spacing: 10px;
    color: #111;
    text-shadow: 4px 2px 0 var(--signal-yellow);
    word-spacing: 30px;
    margin-top: 6px;
  }

  .package-label {
    position: absolute;
    left: 166px;
    top: 698px;
    width: 630px;
    height: 103px;
    background: var(--label-navy);
    display: flex;
    align-items: center;
    justify-content: center;
  }
  .package-label__text {
    font-family: "Montserrat", sans-serif;
    font-weight: 600;
    font-size: 64px;
    line-height: 1;
    color: var(--white);
    -webkit-text-stroke: 1.5px #000;
    letter-spacing: 3px;
  }

  .conditions {
    position: absolute;
    left: 0;
    width: 962px;
    top: 1034px;
    text-align: center;
    font-family: "Bebas Neue", sans-serif;
    font-size: 60px;
    line-height: 1;
    letter-spacing: 5px;
    color: var(--signal-yellow);
  }
  .conditions-rule {
    position: absolute;
    left: 345px;
    top: 1102px;
    width: 312px;
    height: 3px;
    background: linear-gradient(90deg, transparent, rgba(255,255,255,0.9), transparent);
  }
</style>
</head>
<body>
  <main class="poster">
    <div class="streak streak--top"></div>
    <div class="streak streak--upper"></div>
    <div class="streak streak--lower"></div>

    <p class="headline-tag">Now Available*</p>

    <svg class="iris-art" width="962" height="1200" viewBox="0 0 962 1200" role="img" aria-label="Large stylised blue eye iris illustration">
      <defs>
        <radialGradient id="irisFill" cx="0.5" cy="0.5" r="0.55">
          <stop offset="0" stop-color="var(--iris-light)"/>
          <stop offset="0.6" stop-color="var(--iris-mid)"/>
          <stop offset="1" stop-color="var(--iris-deep)"/>
        </radialGradient>
      </defs>
      <ellipse cx="485" cy="579" rx="433" ry="365" fill="url(#irisFill)"/>
    </svg>

    <div class="offer-band">
      <h1 class="offer-band__title">TWO PAIR</h1>
    </div>

    <div class="package-label">
      <h2 class="package-label__text">PACKAGES</h2>
    </div>

    <p class="conditions">*Conditions Apply</p>
    <div class="conditions-rule"></div>
  </main>
</body>
</html>
```